Brochure Design Project

I need a brochure design for a full Hair Salon, located in Rockville MD called Corvina Hair, Nails and Spa.
Please use inovative design (the idea is to target an audience between the age of 19 to 50) keeping our main colors (spring green, grey and white).
we would also like to include the list of services which will be provided when needed.

Target Market(s)

women between 19 to 50 - all ethnical backgrounds

Industry/Entity Type

Hair

Requirements
Nice to have
• we would like to include a blurb, contact info and list of prices of all the services we provided. Also we would like to add the line "se habla espaƱol" anywhere in the brochure.

```html
<!DOCTYPE html>
<html lang="en">
<head>
<meta charset="utf-8">
<title>Corvina Hair, Nails and Spa – Price Brochure</title>
<link rel="stylesheet" href="https://fonts.googleapis.com/css2?family=Archivo+Black&family=Roboto+Slab:wght@700&family=Arimo:wght@400&display=swap">
<style>
  :root {
    --spring-green: #d2e183;
    --logo-green: #b9cf5c;
    --ink: #1d1d1d;
    --grey: #6e6e6e;
    --rule: #2b2b2b;
    --paper: #ffffff;
    --skin-light: #f3dccd;
    --skin-mid: #dcb49c;
    --stone-light: #e2ded6;
    --stone-dark: #8f8a80;
    --petal: #e8789a;
  }
  * { margin: 0; padding: 0; box-sizing: border-box; }
  html, body { width: 1200px; height: 849px; overflow: hidden; background: var(--paper); }
  .brochure {
    position: relative; width: 1200px; height: 849px; overflow: hidden;
    background: var(--paper); color: var(--ink);
    font-family: "Arimo", Arial, sans-serif;
  }
  .panel { position: absolute; top: 0; height: 849px; width: 400px; }
  .panel--nails { left: 0; }
  .panel--hair { left: 400px; background: var(--spring-green); }
  .panel--spa { left: 800px; }

  .brand {
    position: absolute; left: 36px; top: 22px; width: 300px;
    color: var(--logo-green); font-family: "Arimo", Arial, sans-serif; font-weight: 400;
  }
  .brand__name { font-size: 62px; line-height: 66px; letter-spacing: 1px; }
  .brand__tagline { font-size: 17px; line-height: 20px; padding-left: 110px; }

  .category {
    position: absolute; font-family: "Archivo Black", "Arial Black", sans-serif;
    font-size: 30px; line-height: 30px; text-align: center; width: 310px;
    letter-spacing: 0.5px;
  }
  .section-title {
    position: absolute; font-family: "Roboto Slab", Georgia, serif; font-weight: 700;
    font-size: 26px; line-height: 26px; text-align: center; width: 310px;
  }
  .rule { position: absolute; height: 2px; width: 309px; background: var(--rule); }

  .price-list { position: absolute; list-style: none; font-size: 15px; line-height: 19px; }
  .price-list li { position: relative; white-space: nowrap; }
  .price-list .price { position: absolute; top: 0; }
  .price-list--nails .price { left: 256px; }
  .price-list--haircuts .price { left: 256px; }
  .price-list--hair .price { left: 257px; }
  .price-list--perms .price { left: 256px; }
  .price-list--spa .price { left: 256px; }

  .booking { position: absolute; left: 400px; width: 400px; text-align: center; }
  .booking__call { top: 747px; font-size: 19px; line-height: 22px; }
  .booking__phone {
    top: 772px; font-size: 27px; line-height: 34px;
    display: flex; justify-content: center; align-items: center; gap: 6px;
  }
  .booking__web { top: 811px; font-size: 18px; line-height: 22px; }

  .photo { position: absolute; }
  .photo--hands {
    left: 0; top: 622px; width: 305px; height: 227px;
    background: radial-gradient(ellipse at 45% 45%, var(--skin-light) 0%, var(--skin-mid) 55%, rgba(255,255,255,0) 75%);
  }
  .photo--stones {
    left: 830px; top: 652px; width: 370px; height: 197px;
    background:
      radial-gradient(circle at 80% 60%, var(--petal) 0%, rgba(232,120,154,0.6) 14%, rgba(255,255,255,0) 24%),
      radial-gradient(ellipse at 40% 60%, var(--stone-dark) 0%, var(--stone-light) 45%, rgba(255,255,255,0) 72%);
  }
</style>
</head>
<body>
<main class="brochure">

  <section class="panel panel--nails">
    <div class="brand">
      <div class="brand__name">Corvina</div>
      <div class="brand__tagline">Hair, Nails and Spa</div>
    </div>

    <h2 class="category" style="left:46px; top:170px;">NAILS</h2>
    <div class="rule" style="left:47px; top:205px;"></div>
    <h3 class="section-title" style="left:46px; top:213px;">MANICURE</h3>
    <div class="rule" style="left:47px; top:243px;"></div>
    <ul class="price-list price-list--nails" style="left:60px; top:253px;">
      <li>Basic manicure<span class="price">$15</span></li>
      <li>Spa manicure<span class="price">$20</span></li>
      <li>Hot Oil $<span class="price">20</span></li>
      <li>French $20</li>
      <li>Gel color manicure<span class="price">$30</span></li>
      <li>Full set</li>
      <li>(classic manicure and pedicure)<span class="price">$35</span></li>
      <li>Fills<span class="price">$25</span></li>
    </ul>

    <div class="rule" style="left:47px; top:419px;"></div>
    <h3 class="section-title" style="left:46px; top:428px;">PEDICURE</h3>
    <div class="rule" style="left:47px; top:458px;"></div>
    <ul class="price-list price-list--nails" style="left:60px; top:474px;">
      <li>Basic pedicure<span class="price">$25</span></li>
      <li>Warm lotion<span class="price">$35</span></li>
      <li>Spa pedicure<span class="price">$45</span></li>
      <li>Add french<span class="price">$ 5</span></li>
      <li>Polish change<span class="price">$10</span></li>
      <li>Designs<span class="price">$3</span></li>
      <li>Gel color (add $ 12) with pedicure</li>
    </ul>

    <div class="photo photo--hands" role="img" aria-label="Photo of a woman's manicured hands resting on each other"></div>
  </section>

  <section class="panel panel--hair">
    <h2 class="category" style="left:41px; top:25px;">HAIR</h2>
    <div class="rule" style="left:49px; top:61px;"></div>
    <h3 class="section-title" style="left:41px; top:69px;">HAIRCUTS</h3>
    <div class="rule" style="left:49px; top:99px;"></div>
    <ul class="price-list price-list--haircuts" style="left:62px; top:109px;">
      <li>Women’s haircut<span class="price">$30</span></li>
      <li>Men’s haircut $25</li>
      <li>Kid’s haircut (8 &amp; Under)<span class="price">$12</span></li>
      <li>Kid’s haircut (8 to 16) 18</li>
      <li>Girls haircut &amp; blow dry<span class="price">$35</span></li>
      <li>Hair cut &amp; blow dry<span class="price">$50</span></li>
      <li>Roller set &amp; blow dray or flat iron<span class="price">$55</span></li>
      <li>Iron or curling with service<span class="price">$10</span></li>
    </ul>

    <div class="rule" style="left:49px; top:277px;"></div>
    <h3 class="section-title" style="left:41px; top:286px;">CONDITIONING</h3>
    <div class="rule" style="left:49px; top:316px;"></div>
    <ul class="price-list price-list--hair" style="left:52px; top:336px;">
      <li>Hair recovery treatment<span class="price">$20</span></li>
      <li>Deep condition<span class="price">$15</span></li>
      <li>Keratin<span class="price">$300+</span></li>
      <li>Retouch<span class="price">$220</span></li>
    </ul>

    <div class="rule" style="left:49px; top:425px;"></div>
    <h3 class="section-title" style="left:41px; top:433px;">COLORS</h3>
    <div class="rule" style="left:49px; top:463px;"></div>
    <ul class="price-list price-list--hair" style="left:52px; top:477px;">
      <li>All over color<span class="price">$75+</span></li>
      <li>Color touchup<span class="price">$55</span></li>
      <li>Full highlights<span class="price">$125+</span></li>
      <li>Partial highlights<span class="price">$ 75+</span></li>
      <li>Corrective Color<span class="price">$75+</span></li>
      <li>Updos<span class="price">$65+</span></li>
    </ul>

    <div class="rule" style="left:49px; top:600px;"></div>
    <h3 class="section-title" style="left:41px; top:609px;">PERMS</h3>
    <div class="rule" style="left:49px; top:639px;"></div>
    <ul class="price-list price-list--perms" style="left:57px; top:653px;">
      <li>Relaxer with haircut style<span class="price">$85</span></li>
      <li>Curly Perms<span class="price">$95+</span></li>
    </ul>
  </section>

  <p class="booking booking__call">Call in advance for an appointment!</p>
  <p class="booking booking__phone">
    <svg width="26" height="26" viewBox="0 0 26 26" aria-hidden="true">
      <circle cx="13" cy="13" r="11.5" fill="none" stroke="#1d1d1d" stroke-width="1.5"/>
      <path d="M9 7.5c-1.2.6-1.8 1.8-1.4 3.3.9 3.2 3.6 6 6.8 7 1.5.4 2.7-.2 3.3-1.4l-2.2-1.8-1.4 1c-1.7-.8-3-2.1-3.8-3.8l1-1.4z" fill="none" stroke="#1d1d1d" stroke-width="1.3" stroke-linejoin="round"/>
    </svg>
    <span>301-555-0142</span>
  </p>
  <p class="booking booking__web">www.corvinahns.com</p>

  <section class="panel panel--spa">
    <h2 class="category" style="left:52px; top:23px;">SPA</h2>
    <div class="rule" style="left:53px; top:62px;"></div>
    <h3 class="section-title" style="left:52px; top:70px;">FACIALS</h3>
    <div class="rule" style="left:53px; top:100px;"></div>
    <ul class="price-list price-list--spa" style="left:62px; top:110px;">
      <li>European facial<span class="price">$85</span></li>
      <li>Multi Vitamin facial<span class="price">$85</span></li>
      <li>Acne facial<span class="price">$80</span></li>
      <li>Gentleman facial<span class="price">$75</span></li>
      <li>Lunch break facial<span class="price">$45</span></li>
      <li>Teen facial<span class="price">$50</span></li>
      <li>Mini facial<span class="price">$45</span></li>
      <li>Anti aging facial<span class="price">$120</span></li>
      <li>Gold facial<span class="price">$60</span></li>
      <li>Fruit facial<span class="price">$45</span></li>
      <li>Special bridal facial<span class="price">$130</span></li>
    </ul>

    <div class="rule" style="left:53px; top:325px;"></div>
    <h3 class="section-title" style="left:52px; top:330px;">MASSAGES</h3>
    <div class="rule" style="left:53px; top:360px;"></div>
    <ul class="price-list price-list--spa" style="left:66px; top:370px;">
      <li>Scalp massages 10 min<span class="price">$15</span></li>
      <li>Head &amp; neck massage 15 min<span class="price">$20</span></li>
      <li>Back massage 15 min<span class="price">$20</span></li>
      <li>Full body massage 60 min<span class="price">$75</span></li>
      <li>Full body massage 30 min<span class="price">$40</span></li>
      <li>Foot massage 10 min<span class="price">$15</span></li>
      <li>Half leg &amp; foot $15 min<span class="price">$20</span></li>
    </ul>

    <div class="rule" style="left:53px; top:516px;"></div>
    <h3 class="section-title" style="left:52px; top:524px;">MASSAGES</h3>
    <div class="rule" style="left:53px; top:555px;"></div>
    <ul class="price-list price-list--spa" style="left:62px; top:564px;">
      <li>Eyebrow threading<span class="price">$12</span></li>
      <li>Chin Threading<span class="price">$8</span></li>
      <li>Upper lip<span class="price">$7</span></li>
      <li>Lower lip<span class="price">$7</span></li>
      <li>Forehead<span class="price">$10</span></li>
      <li>Side burns<span class="price">$10</span></li>
      <li>Full Face<span class="price">$40+</span></li>
    </ul>

    <div class="photo photo--stones" role="img" aria-label="Photo of stacked spa stones with a pink gerbera flower" style="left:30px;"></div>
  </section>

</main>
</body>
</html>
```